zorvan lumet website design

An IT support and IT Security Company - just use dummy text for now for the design. Examples of sites we like the looks and feel of but need it more professional feel are like: www.kelbrovault.uk.com , www.pravok.co.uk, www.quenthardy.com/professional/, www.vur.com, www.melvish.com,

Best to message me if you have any questions

Target Market(s)

small to medium UK based companies that require IT support services

Industry/Entity Type

It Company

Contact Information for Business Card

use dummy name, telephone and email for now, will provide details later.

Logo Text

zorvan lumet (and then below the logo it should say "your IT, networks and security partner")

Coding

Coded - Design and coding required

Number of Pages Required

5+ page

Colors

Designer to choose colors to be used in the design.

Requirements
Must have
• must be professional, yet simple and clear that this is a serious IT support and IT security company.
Nice to have
• 1)The website homepage must have professional quality pictures of IT support or London city skyline or any picture that projects friendly business partners, professionalism and ready to serve.
• 2) Home page needs to include tabs for following pages 'Services' , 'About Us' , 'Contact Us' 'Home'
• 3) Website built customised using wordpress is ideal and easy for us to manage.
• more room for boxed options from homepage (with pic or image in background)
Should not have
• no checkout trolleys or payment options.

```html
<!DOCTYPE html>
<html lang="en">
<head>
<meta charset="utf-8">
<title>Zorvan Lumet – IT support &amp; security</title>
<link href="https://fonts.googleapis.com/css2?family=Montserrat:wght@400;500;600;700&family=Roboto:wght@400;500;700&display=swap" rel="stylesheet">
<style>
:root{
  --navy:#0b3f7c;
  --blue:#2b7bc4;
  --blue-dark:#0e4a8c;
  --orange:#ee6b2f;
  --band:#f2f2f2;
  --text:#4a4a4a;
  --heading:#222;
  --line:#c9c9c9;
  --white:#fff;
}
*{margin:0;padding:0;box-sizing:border-box}
html,body{width:1200px;height:2757px;overflow:hidden}
body{position:relative;font-family:'Roboto',Arial,sans-serif;color:var(--text);background:var(--white)}
.abs{position:absolute}
.center{left:0;width:1200px;text-align:center}

/* hero */
.hero{left:0;top:0;width:1200px;height:640px;background:linear-gradient(180deg,#0b3a78 0%,#1c5fa3 35%,#c98a62 58%,#2a3550 72%,#101a2c 100%)}
.brand{left:130px;top:14px;font-family:'Montserrat',sans-serif;font-size:29px;font-weight:500;color:var(--white)}
.nav a{position:absolute;top:18px;font-family:'Montserrat',sans-serif;font-size:14px;font-weight:500;color:var(--white);text-decoration:none;line-height:22px}
.nav .current{background:var(--white);color:var(--navy);padding:0 10px}
.search{left:1039px;top:14px;width:28px;height:28px;border:1.5px solid var(--white);border-radius:50%}
.hero-title{top:214px;font-family:'Montserrat',sans-serif;font-size:41px;font-weight:700;color:var(--white)}
.hero-sub{top:272px;font-size:18px;line-height:22px;color:var(--white)}
.btn-hero{left:535px;top:345px;width:130px;height:37px;background:var(--white);color:var(--navy);font-family:'Montserrat',sans-serif;font-weight:700;font-size:14px;line-height:37px;text-align:center;letter-spacing:.5px}
.dot{top:565px;width:11px;height:11px;border-radius:50%;background:var(--white)}
.dot.on{background:var(--orange);border:2px solid var(--white);width:13px;height:13px;top:564px}

/* section headings */
.sec-title{font-family:'Montserrat',sans-serif;font-size:20px;font-weight:700;color:var(--navy);letter-spacing:.5px}
.rule{left:571px;width:58px;height:3px;background:#c5c5c5}

/* services */
.service{top:780px;width:244px;text-align:center}
.service svg{display:block;margin:0 auto}
.service h3{margin-top:22px;font-family:'Montserrat',sans-serif;font-size:13.5px;font-weight:600;color:var(--heading);line-height:16px}
.service p{margin:12px auto 0;width:210px;font-size:11.5px;line-height:15px}
.divider{top:780px;width:1px;height:215px;background:#ddd}

/* welcome */
.band{left:0;width:1200px;background:var(--band)}
.intro{left:390px;top:1170px;width:420px;font-size:12.5px;line-height:19px;text-align:center}
.feature{top:1286px;width:397px;height:259px;color:var(--white)}
.feature.blue{background:linear-gradient(120deg,#2a78c2,#5a98d0)}
.feature.orange{background:linear-gradient(120deg,#ee6b2f,#f39a6a)}
.feature svg{position:absolute;left:50px;top:30px}
.feature h3{position:absolute;left:51px;top:98px;font-family:'Montserrat',sans-serif;font-size:20px;font-weight:500}
.feature p{position:absolute;left:51px;top:124px;width:235px;font-size:11.5px;line-height:15px}
.feature .btn{position:absolute;left:55px;top:190px;width:107px;height:27px;background:var(--white);font-family:'Montserrat',sans-serif;font-size:10px;font-weight:700;line-height:27px;text-align:center;letter-spacing:.5px}
.feature.blue .btn{color:var(--blue)}
.feature.orange .btn{color:var(--orange)}

/* blog */
.post{top:1751px;width:296px;height:348px;background:var(--band)}
.post .photo{height:199px}
.post h3{margin:22px 0 0 26px;font-family:'Roboto',sans-serif;font-size:15px;font-weight:500;color:var(--heading)}
.post p{margin:7px 0 0 26px;width:230px;font-size:12px;line-height:16px}
.post .btn{position:absolute;left:26px;top:291px;width:94px;height:29px;background:var(--blue);color:var(--white);font-family:'Montserrat',sans-serif;font-size:10.5px;font-weight:700;line-height:29px;text-align:center;letter-spacing:.5px}

/* clients */
.client{top:2322px;width:150px;text-align:center;font-family:'Roboto',sans-serif;font-size:19px;font-weight:500;color:#333;line-height:30px}
.client .mark{display:inline-block;width:12px;height:12px;background:#333;margin-right:6px;vertical-align:0}
.arrow{top:2327px}

/* footer */
.footer{left:0;top:2420px;width:1200px;height:337px;background:linear-gradient(180deg,#0e4a8c,#0a3f7a)}
.f-brand{left:129px;top:2472px;font-family:'Montserrat',sans-serif;font-size:37px;font-weight:500;color:var(--white)}
.f-head{font-family:'Montserrat',sans-serif;font-size:11.5px;font-weight:700;color:var(--white);letter-spacing:.5px}
.f-text{font-size:11.5px;line-height:17.5px;color:var(--white)}
.social{top:2541px;width:28px;height:28px;border-radius:50%;background:var(--blue)}
.input{left:860px;top:2514px;width:206px;height:40px;background:var(--white);font-size:12px;color:#666;line-height:40px;padding-left:18px}
.signup{left:860px;top:2573px;width:74px;height:30px;background:var(--orange);color:var(--white);font-family:'Montserrat',sans-serif;font-size:10.5px;font-weight:700;line-height:30px;text-align:center}
.f-line{left:129px;top:2663px;width:942px;height:1px;background:rgba(255,255,255,.25)}
.copy{top:2704px;font-size:11.5px;color:var(--white)}
</style>
</head>
<body>

<!-- hero -->
<div class="abs hero" role="img" aria-label="London skyline at dusk with the river and a lit bridge"></div>
<div class="abs brand">Zorvan Lumet</div>
<nav class="nav">
  <a class="current" style="left:674px">Home</a>
  <a style="left:750px">Services</a>
  <a style="left:845px">About us</a>
  <a style="left:941px">Contact us</a>
</nav>
<div class="abs search">
  <svg width="25" height="25" viewBox="0 0 25 25"><circle cx="11" cy="11" r="4.5" fill="none" stroke="#fff" stroke-width="1.5"/><line x1="14.5" y1="14.5" x2="18" y2="18" stroke="#fff" stroke-width="1.5"/></svg>
</div>
<h1 class="abs center hero-title">IT support &amp; security</h1>
<p class="abs center hero-sub">Sed ut perspiciatis unde omnis iste natus error<br>sit voluptatem accusantium doloremque</p>
<div class="abs btn-hero">READ MORE</div>
<span class="abs dot" style="left:541px"></span>
<span class="abs dot" style="left:566px"></span>
<span class="abs dot on" style="left:590px"></span>
<span class="abs dot" style="left:617px"></span>
<span class="abs dot" style="left:643px"></span>

<!-- services -->
<h2 class="abs center sec-title" style="top:680px">OUR SERVICES</h2>
<div class="abs rule" style="top:716px"></div>

<div class="abs service" style="left:110px">
  <svg width="70" height="70" viewBox="0 0 70 70" fill="none" stroke="#1f6fb8" stroke-width="4"><path d="M14 40V32a21 21 0 0 1 42 0v8"/><rect x="10" y="36" width="10" height="16" rx="4" fill="#1f6fb8"/><rect x="50" y="36" width="10" height="16" rx="4" fill="#1f6fb8"/><path d="M55 52q0 10-14 10"/><circle cx="37" cy="62" r="3" fill="#1f6fb8"/></svg>
  <h3>24/7/365 IT support</h3>
  <p>Sed ut perspiciatis unde omnis iste natus error sit voluptatem accusantium doloremque lau dantium, tota nesciunt. Neque porro quisquam est.</p>
</div>
<div class="abs divider" style="left:353px"></div>
<div class="abs service" style="left:355px">
  <svg width="70" height="70" viewBox="0 0 70 70" fill="none" stroke="#1f6fb8" stroke-width="4"><path d="M16 14l10-2 6 13-7 5q5 11 15 16l5-7 13 6-2 10q-26 2-40-41z" fill="#1f6fb8"/><path d="M40 22a10 10 0 0 1 9 9M41 13a19 19 0 0 1 17 17M42 4a28 28 0 0 1 25 25"/></svg>
  <h3>Unlimited telephone<br>and remote support</h3>
  <p>Sed ut perspiciatis unde omnis iste natus error sit voluptatem accusantium doloremque lau dantium, tota .</p>
</div>
<div class="abs divider" style="left:599px"></div>
<div class="abs service" style="left:603px">
  <svg width="70" height="70" viewBox="0 0 70 70" fill="none" stroke="#1f6fb8" stroke-width="4"><circle cx="35" cy="12" r="6"/><path d="M35 18v14M13 32h44M13 32v12M35 32v12M57 32v12"/><circle cx="13" cy="50" r="6"/><circle cx="35" cy="50" r="6"/><circle cx="57" cy="50" r="6"/></svg>
  <h3>Network Monitoring</h3>
  <p>Sed ut perspiciatis unde omnis iste natus error sit voluptatem accusantium doloremque lau dantium, tota nesciunt. Neque porro quisquam est.</p>
</div>
<div class="abs divider" style="left:853px"></div>
<div class="abs service" style="left:850px">
  <svg width="70" height="70" viewBox="0 0 70 70"><path fill="#1f6fb8" d="M35 5l7 5 9-1 3 8 8 4-1 9 5 7-5 7 1 9-8 4-3 8-9-1-7 5-7-5-9 1-3-8-8-4 1-9-5-7 5-7-1-9 8-4 3-8 9 1z"/><circle cx="35" cy="37" r="16" fill="none" stroke="#fff" stroke-width="3"/><path d="M27 37l6 6 11-12" fill="none" stroke="#fff" stroke-width="4"/></svg>
  <h3>Guaranteed response<br>and fix times</h3>
  <p>Sed ut perspiciatis unde omnis iste natus error sit voluptatem accusantium doloremque lau dantium, tota.</p>
</div>

<!-- welcome -->
<div class="abs band" style="top:1051px;height:557px"></div>
<h2 class="abs center sec-title" style="top:1097px">WELCOME TO OUR SITE</h2>
<div class="abs rule" style="top:1134px"></div>
<p class="abs intro">At vero eos et accusamus et iusto odio dignissimos ducimus qui blanditiis praesentium voluptatum deleniti atque corrupti quos dolores et quas molestias excepturi sint occaecati cupiditate non provident, similique sunt in culpa qui officia deserunt mollitia animi, id est laborum et dolorum fuga.</p>

<div class="abs feature blue" style="left:193px" role="img" aria-label="Blue-tinted photo of hands at a keyboard">
  <svg width="54" height="46" viewBox="0 0 54 46" fill="none" stroke="#fff" stroke-width="3"><rect x="6" y="4" width="42" height="28" rx="2"/><path d="M2 38h50"/><path d="M19 24h16a5 5 0 0 0 0-10 7 7 0 0 0-13 1 4.5 4.5 0 0 0-3 9z"/></svg>
  <h3>Business Continuity</h3>
  <p>At vero eos et accusamus et iusto odio dignissimos ducimus qui blanditiis praese voluptatum deleniti atque corrupti.</p>
  <div class="btn">READ MORE</div>
</div>
<div class="abs feature orange" style="left:617px" role="img" aria-label="Orange-tinted photo of a service desk operator with headset">
  <svg width="60" height="50" viewBox="0 0 60 50" fill="none" stroke="#fff" stroke-width="3"><circle cx="20" cy="30" r="7"/><circle cx="20" cy="30" r="14" stroke-dasharray="5 4" stroke-width="6"/><circle cx="43" cy="13" r="4"/><circle cx="43" cy="13" r="9" stroke-dasharray="4 3" stroke-width="5"/></svg>
  <h3>Outsourced Service Desk</h3>
  <p>At vero eos et accusamus et iusto odio dignissimos ducimus qui blanditiis praese voluptatum deleniti atque corrupti.</p>
  <div class="btn">READ MORE</div>
</div>

<!-- blog -->
<h2 class="abs center sec-title" style="top:1657px">LATEST BLOG</h2>
<div class="abs rule" style="top:1694px"></div>

<article class="abs post" style="left:132px">
  <div class="photo" role="img" aria-label="Office worker at a desktop computer" style="background:linear-gradient(135deg,#e6e8ea,#9ea4aa 60%,#4b5057)"></div>
  <h3>Lorem Ipsum is simply dummy</h3>
  <p>There are many variations of passages of Lorem Ipsum available.</p>
  <div class="btn">READ MORE</div>
</article>
<article class="abs post" style="left:452px">
  <div class="photo" role="img" aria-label="Two colleagues reviewing a tablet in an office" style="background:linear-gradient(135deg,#c9ccd0,#7c8088 55%,#2d2f35)"></div>
  <h3>Lorem Ipsum is simply dummy</h3>
  <p>There are many variations of passages of Lorem Ipsum available.</p>
  <div class="btn">READ MORE</div>
</article>
<article class="abs post" style="left:772px">
  <div class="photo" role="img" aria-label="Hands typing on a laptop in warm light" style="background:linear-gradient(135deg,#f4d3b0,#b08a70 50%,#4a3a34)"></div>
  <h3>Lorem Ipsum is simply dummy</h3>
  <p>There are many variations of passages of Lorem Ipsum available.</p>
  <div class="btn">READ MORE</div>
</article>

<!-- clients -->
<div class="abs band" style="top:2168px;height:252px"></div>
<h2 class="abs center sec-title" style="top:2214px">OUR CLIENTS</h2>
<div class="abs rule" style="top:2251px"></div>
<svg class="abs arrow" style="left:62px" width="16" height="26" viewBox="0 0 16 26"><path d="M12 3L3 13l9 10" fill="none" stroke="#aaa" stroke-width="3"/></svg>
<svg class="abs arrow" style="left:1121px" width="16" height="26" viewBox="0 0 16 26"><path d="M4 3l9 10-9 10" fill="none" stroke="#aaa" stroke-width="3"/></svg>
<div class="abs client" style="left:133px"><span class="mark"></span>Ravelle</div>
<div class="abs client" style="left:318px">Tindoro</div>
<div class="abs client" style="left:525px">Quillet</div>
<div class="abs client" style="left:736px"><span class="mark"></span>Marbeck</div>
<div class="abs client" style="left:942px">Olmsby Works</div>

<!-- footer -->
<footer class="abs footer" role="img" aria-label="Faint city skyline behind the footer"></footer>
<div class="abs f-brand">Zorvan Lumet</div>
<div class="abs f-head" style="left:131px;top:2549px">FOLLOW US</div>
<span class="abs social" style="left:220px" aria-label="Social profile one"></span>
<span class="abs social" style="left:256px" aria-label="Social profile two"></span>
<span class="abs social" style="left:291px;background:#1b3d7a" aria-label="Social profile three"></span>

<div class="abs f-head" style="left:437px;top:2472px">CONTACT US</div>
<svg class="abs" style="left:437px;top:2508px" width="10" height="13" viewBox="0 0 10 13"><path d="M5 0a5 5 0 0 0-5 5c0 4 5 8 5 8s5-4 5-8a5 5 0 0 0-5-5z" fill="#fff"/><circle cx="5" cy="5" r="2" fill="#0e4a8c"/></svg>
<p class="abs f-text" style="left:459px;top:2503px">58 Harlow Mews<br>Coldbridge, KT4 7QS</p>
<svg class="abs" style="left:437px;top:2558px" width="11" height="11" viewBox="0 0 11 11"><path d="M1 1l3-1 2 3-2 1.5q1.5 3 4 4L9.5 7l2 2-1 2Q2 10 1 1z" fill="#fff"/></svg>
<p class="abs f-text" style="left:459px;top:2554px">020 7946 0312</p>
<svg class="abs" style="left:437px;top:2594px" width="12" height="9" viewBox="0 0 12 9"><rect width="12" height="9" fill="#fff"/><path d="M0 0l6 5 6-5" fill="none" stroke="#0e4a8c" stroke-width="1.2"/></svg>
<p class="abs f-text" style="left:459px;top:2590px">info@zorvanlumet.com</p>

<div class="abs f-head" style="left:682px;top:2472px">MENU</div>
<p class="abs f-text" style="left:682px;top:2503px">Home<br>Services<br>About us<br>Contact us</p>

<div class="abs f-head" style="left:858px;top:2472px">NEWSLETTER</div>
<div class="abs input">E mail id</div>
<div class="abs signup">SIGNUP</div>

<div class="abs f-line"></div>
<p class="abs center copy">Copyrights @ 2018 All Rights Reserved</p>

</body>
</html>
```